Need to drive pregnant women to my 3d4d ultrasound studio where i provide 4d ultrasound with hyperalistic imaging and gender reveals

Industry/Entity Type

Healthcare

Font styles to use
Decorative
Script

Requirements
Must have
• My Company name Cielo de Nuestra Espera 4D. EVERYTHING HAS TO BE IN SPANISH
Nice to have
• SIMPLE AND NOT TOO BUSY
Should not have
• website

```html
<!DOCTYPE html>
<html lang="es">
<head>
<meta charset="UTF-8">
<title>Cielo de Nuestra Espera 4D</title>
<link href="https://fonts.googleapis.com/css2?family=Kanit:wght@700&family=Poppins:wght@500;700&display=swap" rel="stylesheet">
<style>
  :root {
    --page: #eef0f3;
    --board: #f8dcbf;
    --brown: #7a3d12;
    --navy: #1c2f8c;
    --navy-deep: #0f1f6b;
    --white: #fffaf2;
    --scan-light: #d9893a;
    --scan-dark: #6e3308;
    --skin-light: #f6d3c3;
    --skin-dark: #d99c86;
  }
  * { margin: 0; padding: 0; box-sizing: border-box; }
  html, body { width: 1200px; height: 900px; overflow: hidden; background: var(--page); }
  .billboard {
    position: absolute;
    left: 30px; top: 255px;
    width: 1140px; height: 390px;
    background: var(--board);
    overflow: hidden;
  }
  .heart { position: absolute; }
  .heart--scan { left: 28px; top: 40px; width: 330px; height: 310px; }
  .heart--newborn { left: 870px; top: 130px; width: 250px; height: 235px; }
  .headline {
    position: absolute;
    left: 330px; top: 40px; width: 560px;
    text-align: center;
    font-family: 'Kanit', sans-serif;
    font-weight: 700;
    font-size: 84px;
    line-height: 0.86;
    letter-spacing: -1px;
    color: var(--brown);
    text-transform: uppercase;
  }
  .contact-band {
    position: absolute;
    left: 340px; top: 312px;
    width: 540px; height: 78px;
  }
  .contact-band svg.band-shape { position: absolute; inset: 0; }
  .contact-text {
    position: absolute; inset: 0;
    display: flex; align-items: center; justify-content: center; gap: 16px;
    color: var(--white);
    font-family: 'Poppins', sans-serif;
    padding-top: 4px;
  }
  .contact-label { font-weight: 500; font-size: 21px; }
  .contact-phone { display: flex; align-items: center; gap: 8px; font-weight: 700; font-size: 34px; letter-spacing: 0.5px; }
  .contact-phone svg { width: 26px; height: 26px; }
</style>
</head>
<body>
  <main class="billboard">
    <svg class="heart heart--scan" viewBox="0 0 100 94" role="img" aria-label="Imagen de ecografía 4D de un bebé en el vientre, en forma de corazón">
      <defs>
        <radialGradient id="scanFill" cx="45%" cy="45%" r="65%">
          <stop offset="0" stop-color="var(--scan-light)"/>
          <stop offset="1" stop-color="var(--scan-dark)"/>
        </radialGradient>
      </defs>
      <path d="M50 90 C20 70 3 52 3 30 C3 14 15 4 29 4 C39 4 46 10 50 18 C54 10 61 4 71 4 C85 4 97 14 97 30 C97 52 80 70 50 90 Z"
            fill="url(#scanFill)" stroke="var(--white)" stroke-width="2.2"/>
    </svg>

    <h1 class="headline">Cielo de<br>Nuestra<br>Espera 4D</h1>

    <div class="contact-band">
      <svg class="band-shape" viewBox="0 0 540 78" preserveAspectRatio="none" aria-hidden="true">
        <defs>
          <linearGradient id="bandFill" x1="0" x2="1">
            <stop offset="0" stop-color="var(--navy-deep)"/>
            <stop offset="0.5" stop-color="var(--navy)"/>
            <stop offset="1" stop-color="var(--navy-deep)"/>
          </linearGradient>
        </defs>
        <path d="M30 0 H510 Q520 0 524 10 L540 78 H0 L16 10 Q20 0 30 0 Z" fill="url(#bandFill)"/>
      </svg>
      <div class="contact-text">
        <span class="contact-label">Para orientación</span>
        <span class="contact-phone">
          <svg viewBox="0 0 24 24" aria-hidden="true"><path fill="var(--white)" d="M6.6 10.8a15.1 15.1 0 0 0 6.6 6.6l2.2-2.2a1 1 0 0 1 1-.25 11.4 11.4 0 0 0 3.6.57 1 1 0 0 1 1 1V20a1 1 0 0 1-1 1A17 17 0 0 1 3 4a1 1 0 0 1 1-1h3.5a1 1 0 0 1 1 1c0 1.25.2 2.45.57 3.6a1 1 0 0 1-.25 1z"/></svg>
          555-014-2278
        </span>
      </div>
    </div>

    <svg class="heart heart--newborn" viewBox="0 0 100 94" role="img" aria-label="Fotografía de un bebé recién nacido dormido, en forma de corazón">
      <defs>
        <radialGradient id="skinFill" cx="45%" cy="45%" r="65%">
          <stop offset="0" stop-color="var(--skin-light)"/>
          <stop offset="1" stop-color="var(--skin-dark)"/>
        </radialGradient>
      </defs>
      <path d="M50 90 C20 70 3 52 3 30 C3 14 15 4 29 4 C39 4 46 10 50 18 C54 10 61 4 71 4 C85 4 97 14 97 30 C97 52 80 70 50 90 Z"
            fill="url(#skinFill)" stroke="var(--white)" stroke-width="2.6"/>
    </svg>
  </main>
</body>
</html>
```